The Korvane LLC Asset Classes

I'm looking for for two designs here to go into powerpoint and potentially as a standalone PDF. My company does wealth management.
Graphic Image #1
I break down the investment world into 4 broad categories
-Preservation
-Capital Markets
-Real Estate
-Alternatives
In each broad category, there are subcategories:
Preservation: cash, checking/savings accounts, money market accounts, CD's, and fixed annuities.
Capital Markets: Publicly traded stocks and bonds
Real Estate: single-family residence, retail, industrial, multifamily, and office
Alternatives: private equity, private credit, cryptocurrency, asset-backed loans, tax liens, oil & gas, litigation finance, and royalties
Graphic 2: Please see the bottom f page 1 of the Tessolin Decks PDF.
Just like in graphic one, you have 4 categories of the Capital Markets and their respective subcategories
Category 1: Domestic Stocks: Subcategories are Large, mid, and small size companies
Category 2: International Stocks: Subcategories are Large, Mid/Small and by region - Developed and Emerging
Category 3: Fixed Income: You have subcategories like corporate, municipal, government, domestic, international
Category 4: Alternatives: The subcategories are metals and real estate
---------------------
I'm looking to create a graphic (either pie chart, or a circle broken into parts or some other clever way to illustrate this) to clearly illustrate both of these universes in a clean, professional, slick manner.
Target Market(s)
Investors
Colors
Designer to choose colors to be used in the design.
Requirements
Must have
- Clean
- professional
- Easy to read
- Creative
- Visually appealling
Nice to have
- I have attached my logo and some marketing materials so you can get a feel of what I am doing. Maybe you can clean this up too!

```html
<!DOCTYPE html>
<html lang="en">
<head>
<meta charset="utf-8">
<title>Korvane LLC – Capital Markets Categories</title>
<link rel="stylesheet" href="https://fonts.googleapis.com/css2?family=Open+Sans:wght@400;600;700&family=Nunito:wght@900&display=swap">
<style>
  :root {
    --page-bg: #e4e5e7;
    --slide-bg: #ffffff;
    --accent-orange: #f0873a;
    --navy: #02335f;
    --royal: #086aad;
    --sky: #18a3de;
    --light-sky: #72bfe0;
    --text-grey: #4a4a4a;
    --brand-teal: #12588a;
  }
  html, body {
    margin: 0;
    width: 1200px;
    height: 1000px;
    overflow: hidden;
    background: var(--page-bg);
  }
  .slide {
    position: absolute;
    left: 20px;
    top: 65px;
    width: 1160px;
    height: 870px;
    background: var(--slide-bg);
    box-shadow: 0 4px 14px rgba(0,0,0,0.18);
  }
  .slide svg { display: block; width: 100%; height: 100%; }
  .slide-title {
    font-family: "Open Sans", sans-serif;
    font-weight: 400;
    font-size: 62px;
    fill: var(--accent-orange);
  }
  .brand-name {
    font-family: "Open Sans", sans-serif;
    font-weight: 700;
    fill: var(--brand-teal);
  }
  .segment-label {
    font-family: "Nunito", sans-serif;
    font-weight: 900;
    font-size: 34px;
    fill: #ffffff;
    text-anchor: middle;
  }
  .callout-text {
    font-family: "Open Sans", sans-serif;
    font-weight: 600;
    font-size: 26px;
    fill: var(--text-grey);
  }
  .leader { stroke: var(--accent-orange); stroke-width: 1.6; fill: none; }
  .leader-dot { fill: var(--accent-orange); }
</style>
</head>
<body>
<div class="slide">
  <svg viewBox="0 0 1750 1313" xmlns="http://www.w3.org/2000/svg">
    <defs>
      <filter id="soft-shadow" x="-20%" y="-20%" width="140%" height="140%">
        <feDropShadow dx="-14" dy="20" stdDeviation="22" flood-color="#000" flood-opacity="0.22"/>
      </filter>
      <radialGradient id="hub-fill" cx="50%" cy="35%" r="70%">
        <stop offset="0%" stop-color="#ffffff"/>
        <stop offset="100%" stop-color="#dcdcdf"/>
      </radialGradient>
    </defs>

    <text class="slide-title" x="70" y="137">Capital Markets Categories</text>

    <g class="brand-lockup">
      <circle cx="1292" cy="112" r="34" fill="var(--brand-teal)"/>
      <text class="brand-name" x="1342" y="128" font-size="44">Korvane LLC</text>
    </g>

    <g class="category-wheel" filter="url(#soft-shadow)">
      <path class="segment domestic" fill="var(--navy)" d="M897,712 L897,242 A470,470 0 0 0 427,712 Z"/>
      <path class="segment international" fill="var(--royal)" d="M897,712 L897,272 A445,445 0 0 1 1347,712 Z"/>
      <path class="segment fixed-income" fill="var(--light-sky)" d="M897,712 L1307,712 A410,410 0 0 1 897,1122 Z"/>
      <path class="segment alternatives" fill="var(--sky)" d="M897,712 L897,1142 A430,430 0 0 1 467,712 Z"/>
    </g>

    <g class="hub" filter="url(#soft-shadow)">
      <circle cx="897" cy="712" r="172" fill="url(#hub-fill)"/>
    </g>
    <circle cx="897" cy="712" r="150" fill="none" stroke="var(--accent-orange)" stroke-width="5" opacity="0.85"/>
    <text class="brand-name" x="897" y="722" font-size="30" text-anchor="middle">Korvane LLC</text>

    <text class="segment-label" x="660" y="497">Domestic</text>
    <text class="segment-label" x="660" y="537">Stocks</text>
    <text class="segment-label" x="1087" y="497">International</text>
    <text class="segment-label" x="1087" y="537">Stocks</text>
    <text class="segment-label" x="705" y="932">Alternatives</text>
    <text class="segment-label" x="1083" y="917">Fixed</text>
    <text class="segment-label" x="1083" y="957">Income</text>

    <g class="callout domestic-callout">
      <polyline class="leader" points="301,364 585,364"/>
      <circle class="leader-dot" cx="301" cy="364" r="5"/>
      <text class="callout-text" x="245" y="414">Large, mid,</text>
      <text class="callout-text" x="245" y="448">and small</text>
      <text class="callout-text" x="245" y="482">companies</text>
    </g>

    <g class="callout international-callout">
      <polyline class="leader" points="1090,315 1427,315 1427,358"/>
      <circle class="leader-dot" cx="1427" cy="360" r="5"/>
      <text class="callout-text" x="1330" y="399">• Large, mid/small</text>
      <text class="callout-text" x="1330" y="434">• Developed and</text>
      <text class="callout-text" x="1356" y="468">Emerging</text>
    </g>

    <g class="callout alternatives-callout">
      <polyline class="leader" points="530,938 309,938 309,980"/>
      <circle class="leader-dot" cx="309" cy="982" r="5"/>
      <text class="callout-text" x="245" y="1051">• Metals</text>
      <text class="callout-text" x="245" y="1085">• Real Estate</text>
    </g>

    <g class="callout fixed-income-callout">
      <polyline class="leader" points="1200,987 1382,987"/>
      <circle class="leader-dot" cx="1382" cy="987" r="5"/>
      <text class="callout-text" x="1306" y="1051">• Corporate</text>
      <text class="callout-text" x="1306" y="1085">• Municipal</text>
      <text class="callout-text" x="1306" y="1119">• Government</text>
      <text class="callout-text" x="1306" y="1153">• Domestic</text>
      <text class="callout-text" x="1306" y="1187">• International</text>
    </g>
  </svg>
</div>
</body>
</html>
```